Design a single page Shopify store web page

We are looking to have a page designed for a single page Shopify store with 2 products. We already have a basic structure that we like, though we are open to suggestions. We are looking for somebody to provide a design/color scheme that we can then implement using Shopify's templating system. We can handle the implementation(HTML / CSS / jS) as we already have 2 web developers on the team, but have not been able to find a design we liked.

The job would consist of providing a mockup (photoshop or otherwise) and any vector graphics you choose to create for the site (we can provide product photos and other images).

You can also look at http://brickdune.com.au for some of our design direction we have used so far

Target Market(s)

Young Australian Males (18 - 49)

Industry/Entity Type

Store

Number of Pages Required

1 page

Font styles to use
Serif
Sans Serif

Requirements
Must have
• Single Page Design
• E-commerce Product Purchase
• Manly (whatever interpretation of that you have)

```html
<!DOCTYPE html>
<html lang="en">
<head>
<meta charset="utf-8">
<title>Brick Dune — Automate Your Life</title>
<link rel="stylesheet" href="https://fonts.googleapis.com/css2?family=Questrial&family=Open+Sans:wght@300;400;600;700&family=Lato:wght@400;700&display=swap">
<style>
:root{
  --ink:#222324;
  --ink-deep:#1a1a1b;
  --ink-soft:#2b2c2d;
  --teal:#1b8a85;
  --teal-dark:#15706c;
  --grey-circle:#8b8f93;
  --white:#ffffff;
  --text-light:#d9dcdc;
  --text-dim:#a8abad;
  --text-dark:#2a2a2a;
  --text-body:#777;
  --line:#d4d4d4;
}
*{margin:0;padding:0;box-sizing:border-box}
html,body{width:1200px;height:2799px;overflow:hidden}
body{position:relative;background:var(--ink);font-family:"Open Sans",Arial,sans-serif;color:var(--white)}
.abs{position:absolute}
section{position:absolute;left:0;width:1200px;overflow:hidden}

/* HERO */
.hero{top:0;height:761px;background:var(--ink-deep)}
.hero-bg{position:absolute;inset:0}
.hero-photo{position:absolute;left:0;top:0;width:1200px;height:761px;
  background:linear-gradient(160deg,#3a3530 0%,#1c1a18 45%,#6b6558 70%,#2a2622 100%);
  clip-path:polygon(858px 0,1200px 0,1200px 761px,407px 761px)}
.logo{position:absolute;left:100px;top:36px;font-family:"Questrial",sans-serif;font-size:54px;letter-spacing:3px;color:#cfd2d3;line-height:1}
.nav{position:absolute;top:46px;left:578px;display:flex;align-items:center;font-size:13px;color:var(--text-light)}
.nav a{color:inherit;text-decoration:none}
.nav .pill{border:1px solid #9ea1a3;border-radius:16px;padding:6px 12px;margin-right:18px}
.nav .link{margin-right:30px}
.signup{position:absolute;left:942px;top:44px;width:157px;height:32px;border-radius:16px;background:var(--teal);color:var(--white);font-size:13px;display:flex;align-items:center;justify-content:center}
.hero-rule{position:absolute;left:100px;top:123px;width:1000px;border-top:1px dashed #5a5c5e}
.hero-title{position:absolute;left:104px;top:282px;font-family:"Questrial",sans-serif;font-size:44px;line-height:50px;color:var(--white);font-weight:400}
.hero-underline{position:absolute;left:104px;top:400px;width:344px;height:2px;background:linear-gradient(90deg,var(--teal) 0 70px,#3a3c3e 70px)}
.hero-sub{position:absolute;left:104px;top:424px;width:360px;font-size:21px;line-height:31px;color:var(--text-light);font-weight:300}
.arrow{position:absolute;top:385px;width:40px;height:40px;border-radius:50%;border:1px solid #555}

/* HOW IT WORKS */
.how{top:761px;height:493px;background:var(--teal)}
.section-title{position:absolute;left:0;width:1200px;text-align:center;font-weight:300;font-size:36px}
.how .section-title{top:68px}
.step-circle{position:absolute;width:112px;height:112px;border-radius:50%;display:flex;align-items:center;justify-content:center}
.step-circle.white{background:var(--white)}
.step-circle.grey{background:var(--grey-circle)}
.step-title{position:absolute;font-family:"Lato",sans-serif;font-size:26px;color:var(--white)}
.step-text{position:absolute;width:210px;font-family:"Lato",sans-serif;font-size:14px;line-height:20px;color:#e4f2f1}

/* PLANS */
.plans{top:1254px;height:612px;background:var(--ink)}
.plans .section-title{top:24px}
.plan-card{position:absolute;top:104px;width:488px;height:374px;background:var(--white);color:var(--text-dark)}
.plan-name{position:absolute;left:0;top:18px;width:100%;text-align:center;font-size:26px;font-weight:400}
.plan-photo{position:absolute;left:21px;top:75px;width:278px;height:278px}
.plan-thumb{position:absolute;left:318px;width:149px;height:50px}
.plan-price{position:absolute;left:318px;top:220px;font-size:40px;font-weight:700}
.plan-btn{position:absolute;left:318px;top:305px;width:149px;height:48px;background:var(--teal);color:var(--white);font-weight:700;font-size:23px;display:flex;align-items:center;justify-content:center;letter-spacing:.5px}
.perks{position:absolute;top:505px;left:0;width:1200px;height:30px}
.perk{position:absolute;display:flex;align-items:center;font-size:21px;color:#e9eaea}
.perk svg{margin-right:12px}
.perk-sep{position:absolute;top:3px;width:1px;height:26px;background:#777}

/* FAQ */
.faq{top:1866px;height:580px;background:var(--white);color:var(--text-dark)}
.faq .section-title{top:44px;color:#444}
.faq-box{position:absolute;width:311px;height:136px;border:1px solid var(--line);text-align:center;padding:16px 14px 0}
.faq-q{font-size:18px;font-weight:600;line-height:22px;color:#222;height:50px;display:flex;align-items:center;justify-content:center}
.faq-a{font-size:11.5px;line-height:17px;color:var(--text-body);margin-top:2px}
.view-all{position:absolute;left:534px;top:459px;width:132px;height:34px;background:var(--teal);color:var(--white);font-size:14px;font-weight:600;display:flex;align-items:center;justify-content:center}

/* FOOTER */
.footer{top:2446px;height:353px;background:var(--ink-deep)}
.footer-left{position:absolute;inset:0;background:var(--ink-soft);clip-path:polygon(0 0,690px 0,463px 353px,0 353px)}
.about-title{position:absolute;left:100px;top:36px;font-size:36px;font-weight:300}
.about-text{position:absolute;left:100px;top:98px;width:404px;font-size:12.5px;line-height:17.5px;color:var(--text-dim)}
.read-more{position:absolute;left:100px;top:278px;width:126px;height:30px;border:1px solid #bbb;font-size:13px;display:flex;align-items:center;justify-content:center;color:#eee}
.foot-info{position:absolute;left:634px;width:500px;text-align:center;font-size:12.5px;color:#d2d4d5}
.foot-links span{margin:0 7px}
.pay-row{position:absolute;left:780px;top:205px;display:flex;gap:10px}
.pay{width:42px;height:26px;background:#e7e9ea;border-radius:2px}
.social-row{position:absolute;left:829px;top:253px;display:flex;gap:8px}
.social{width:22px;height:22px;border-radius:50%;background:#eceeef}
</style>
</head>
<body>

<section class="hero">
  <div class="hero-photo" role="img" aria-label="Photo of a male model in green briefs wearing headphones, seated against a dark backdrop"></div>
  <svg class="hero-bg" width="1200" height="761" aria-hidden="true">
    <polygon points="0,0 858,0 407,761 0,761" fill="#232425"/>
  </svg>
  <div class="logo">BRICK DUNE</div>
  <nav class="nav">
    <a class="pill" href="#how">How It Works</a>
    <a class="link" href="#plans">Plans</a>
    <a class="link" href="#faq">FAQ</a>
    <a href="#about">About Us</a>
  </nav>
  <a class="signup">Signup Now</a>
  <div class="hero-rule"></div>
  <h1 class="hero-title">AUTOMATE YOUR<br>LIFE</h1>
  <div class="hero-underline"></div>
  <p class="hero-sub">New Underwear And Socks Delivered to your door when you need it</p>
  <div class="arrow" style="left:30px">
    <svg width="40" height="40" viewBox="0 0 40 40"><path d="M24 14l-6 6 6 6M18 20h10" stroke="#666" stroke-width="2" fill="none"/></svg>
  </div>
  <div class="arrow" style="left:1131px">
    <svg width="40" height="40" viewBox="0 0 40 40"><path d="M16 14l6 6-6 6" stroke="#666" stroke-width="2" fill="none"/></svg>
  </div>
</section>

<section class="how" id="how">
  <h2 class="section-title">How It Works</h2>
  <svg class="abs" style="left:0;top:0" width="1200" height="493" aria-hidden="true">
    <path d="M172 316 C 210 420, 330 380, 402 351" stroke="#d6eeec" stroke-width="1.5" stroke-dasharray="4 4" fill="none"/>
    <path d="M530 290 C 590 200, 650 190, 720 206 S 800 230, 815 240" stroke="#d6eeec" stroke-width="1.5" stroke-dasharray="4 4" fill="none"/>
  </svg>

  <div class="step-circle white" style="left:108px;top:204px">
    <svg width="40" height="44" viewBox="0 0 40 44"><path d="M14 4a3 3 0 016 0v14l10 2c3 .6 5 3 4.5 6L32 40H14L5 27a3 3 0 014.5-4l4.5 4z" fill="var(--teal)"/></svg>
  </div>
  <div class="step-title" style="left:243px;top:196px">Choose a Plan</div>
  <div class="step-text" style="left:245px;top:240px;width:200px">There will be palns for all budgets and styles</div>

  <div class="step-circle grey" style="left:455px;top:295px">
    <svg width="46" height="40" viewBox="0 0 46 40"><path d="M4 21l12 12L42 6" stroke="#fff" stroke-width="6" fill="none" stroke-linecap="round" stroke-linejoin="round"/></svg>
  </div>
  <div class="step-title" style="left:580px;top:293px">Choose How Often</div>
  <div class="step-text" style="left:583px;top:337px;width:250px">Decide whether you would like to receve new packages every 3 or 6 months</div>

  <div class="step-circle grey" style="left:799px;top:204px">
    <svg width="46" height="40" viewBox="0 0 46 40"><path d="M4 14h8l22-10v32L12 26H4z" fill="#fff"/><path d="M12 26l3 10h6l-3-10z" fill="#fff"/></svg>
  </div>
  <div class="step-title" style="left:931px;top:200px">Get Your Pack</div>
  <div class="step-text" style="left:933px;top:244px;width:170px">We'll send out your first pack right away and then again every 3 or 6 months</div>
</section>

<section class="plans" id="plans">
  <h2 class="section-title">Plans</h2>

  <div class="plan-card" style="left:100px">
    <div class="plan-name">Comfort</div>
    <div class="plan-photo" role="img" aria-label="Photo of a male model in white trunks" style="background:linear-gradient(135deg,#e8e8e8,#a9a7a4 60%,#d9d8d6)"></div>
    <div class="plan-thumb" role="img" aria-label="Close-up of dark underwear" style="top:75px;background:linear-gradient(90deg,#2a2624,#6e5a50)"></div>
    <div class="plan-thumb" role="img" aria-label="Close-up of trunks on a model" style="top:144px;background:linear-gradient(90deg,#1c1a18,#4b3a30)"></div>
    <div class="plan-price">$30</div>
    <div class="plan-btn">GET IT!</div>
  </div>

  <div class="plan-card" style="left:614px">
    <div class="plan-name">Style</div>
    <div class="plan-photo" role="img" aria-label="Photo of a male model in navy briefs by the sea" style="background:linear-gradient(180deg,#e9eef0 0%,#cfd8dc 40%,#2a7fb0 62%,#1c5f8e 100%)"></div>
    <div class="plan-thumb" role="img" aria-label="Model in light briefs" style="top:75px;background:linear-gradient(90deg,#e4e8ea,#a8b4bc)"></div>
    <div class="plan-thumb" role="img" aria-label="Model in green briefs" style="top:144px;background:linear-gradient(90deg,#1e1d1c,#6f7a3a)"></div>
    <div class="plan-price">$30</div>
    <div class="plan-btn">GET IT!</div>
  </div>

  <div class="perks">
    <div class="perk" style="left:97px">
      <svg width="30" height="22" viewBox="0 0 30 22"><path d="M10 2h18v14H10zM2 8h7v8H1v-4z" fill="#fff"/><circle cx="7" cy="18" r="3" fill="#fff"/><circle cx="23" cy="18" r="3" fill="#fff"/></svg>Free Shipping</div>
    <div class="perk-sep" style="left:304px"></div>
    <div class="perk" style="left:345px">
      <svg width="22" height="22" viewBox="0 0 22 22"><circle cx="11" cy="11" r="10" fill="#fff"/><path d="M7 7l8 8M15 7l-8 8" stroke="var(--ink)" stroke-width="2.4"/></svg>Cancel Whenever</div>
    <div class="perk-sep" style="left:580px"></div>
    <div class="perk" style="left:619px">
      <svg width="24" height="24" viewBox="0 0 24 24"><path d="M20 12a8 8 0 11-3-6.2" stroke="#fff" stroke-width="3" fill="none"/><path d="M14 2h7v7z" fill="#fff"/></svg>Easy Returns</div>
    <div class="perk-sep" style="left:806px"></div>
    <div class="perk" style="left:832px">
      <svg width="24" height="24" viewBox="0 0 24 24"><circle cx="11" cy="12" r="9" stroke="#fff" stroke-width="2" fill="none"/><path d="M6 12l5 5 11-13" stroke="#fff" stroke-width="3" fill="none"/></svg>Satisfaction Guaranteed</div>
  </div>
</section>

<section class="faq" id="faq">
  <h2 class="section-title">FAQ</h2>
  <div class="faq-box" style="left:100px;top:114px"><div class="faq-q">What is Brick Dune?</div><p class="faq-a">Donec interdum vulputate accumsan. Sed vitae tortor sit amet arcu tempus imperdiet. Fusce viverra eu est at semper.</p></div>
  <div class="faq-box" style="left:444px;top:114px"><div class="faq-q">What is your<br>Satisfaction Guarantee?</div><p class="faq-a">Donec interdum vulputate accumsan. Sed vitae tortor sit amet arcu tempus imperdiet. Fusce viverra eu est at semper.</p></div>
  <div class="faq-box" style="left:789px;top:114px"><div class="faq-q">Shipping Policy?</div><p class="faq-a">Donec interdum vulputate accumsan. Sed vitae tortor sit amet arcu tempus imperdiet. Fusce viverra eu est at semper.</p></div>
  <div class="faq-box" style="left:100px;top:284px"><div class="faq-q">What is Brick Dune?</div><p class="faq-a">Donec interdum vulputate accumsan. Sed vitae tortor sit amet arcu tempus imperdiet. Fusce viverra eu est at semper.</p></div>
  <div class="faq-box" style="left:444px;top:284px"><div class="faq-q">What is your<br>Satisfaction Guarantee?</div><p class="faq-a">Donec interdum vulputate accumsan. Sed vitae tortor sit amet arcu tempus imperdiet. Fusce viverra eu est at semper.</p></div>
  <div class="faq-box" style="left:789px;top:284px"><div class="faq-q">Shipping Policy?</div><p class="faq-a">Donec interdum vulputate accumsan. Sed vitae tortor sit amet arcu tempus imperdiet. Fusce viverra eu est at semper.</p></div>
  <div class="view-all">VIEW ALL</div>
</section>

<section class="footer" id="about">
  <div class="footer-left"></div>
  <h2 class="about-title">About Us</h2>
  <p class="about-text">Lorem ipsum dolor sit amet, consectetur adipiscing elit. Phasellus vitae nisi ut nunc scelerisque fermentum a sit amet nunc. Aenean ut felis ultricies, consectetur diam quis, volutpat erat. Quisque molestie hendrerit ultricies. Pellentesque est dui congue at dui id, accumsan ultrices turpis. Integer interdum eu elit vel auctor. In eu mollis lacus. Fusce dui sapien, congue rhoncus sapien quis, accumsan euismod tellus.</p>
  <div class="read-more">Read More</div>

  <div class="foot-info foot-links" style="top:94px">Shipping<span>/</span>Returns<span>/</span>Payment<span>/</span>Terms of Use<span>/</span>Privacy Policy</div>
  <div class="foot-info" style="top:128px">E-mail : info@brickdune.com.au</div>
  <div class="foot-info" style="top:160px">Copyright ©&nbsp; 2014&nbsp; Brick Dune.&nbsp; All rights reserved</div>
  <div class="pay-row" aria-label="Accepted payment methods">
    <div class="pay"></div><div class="pay"></div><div class="pay"></div><div class="pay"></div>
  </div>
  <div class="social-row" aria-label="Social links">
    <div class="social"></div><div class="social"></div><div class="social"></div><div class="social"></div>
  </div>
</section>

</body>
</html>
```